Mortgage Protection Insurance Flyer

The target audience are new home owners so the design needs to be clean and simple.

This a primarily for Final Expense Insurance, but need an area where it says "We Also Specialize In:"
- Medicare Supplement Insurance (MediGap)
- Annuities
- Final Expense

All flyer versions need to be editable. Colors to be used are red, white or black. Refer to my website for colors and photos (corvantshield.com). Will attach my logo and a flyer that I found online that is the format that I am looking for (for 8.5 in. x 11 in version). Need flyer in standard letter size 8.5 in. x11 in. but also in 8.5 in. x 5.5 in and 5.0 in. x 8.0 in. All sizes to be portrait oriented. If picked as winning design, need all flyer versions in full color, also in grey scale and files in all industry file types.

Content can be taken from my website..... corvantshield.com

Do NOT submit if you are not willing to provide all versions as described above for the original project price.

Must use royalty-free stock photos please.

Target Market(s)

New homeowners looking for insurance to protect there mortgage payments

Industry/Entity Type

Life Insurance

Colors
f69fa3

Requirements
Must have
• Colors to be used are red, white or black.
• Need flyer in standard letter size 8.5 in. x11 in. but also in 3.5 in. x 8.5 in (Full Bleed 3.75 in by 8.75 in.) and 4.0 in. x 6.0 in. (Full Bleed 4.12 in x 6.12 in) Each design tailored to the size dimensions (So no squeezing 8.5 x 11 design into a 4.0 x 6.0 space.) All sizes to be portrait oriented. If picked as winning design, need all flyer versions in full color, also in grey scale and files in all file types.
• Do not need physical address on flyer, do need email address on flyer though - tkelwer@corvantshield.com
• So phone number should be prominent, email address and website address should also be contact area.
• If you can not agree to terms above, do not submit any designs.
• Need facebook & twitter logos somewhere in contact info area.
Nice to have
• See sample flyers I have attached.
• White background with red used as primary graphic color and black used as secondary graphic if needed.
• font to be used should similar to one used in logo.

```html
<!DOCTYPE html>
<html lang="en">
<head>
<meta charset="utf-8">
<title>Corvant Shield – Final Expense Insurance Flyer</title>
<link href="https://fonts.googleapis.com/css2?family=Anton&family=Lato:wght@400;700;900&display=swap" rel="stylesheet">
<style>
  :root{
    --red:#e3060b;
    --red-deep:#a8080c;
    --ink:#1d1d1f;
    --charcoal:#3a3a3c;
    --grey-bar:#cfcfd1;
    --paper:#ffffff;
    --stage:#ececec;
    --text:#3b3b3b;
  }
  *{box-sizing:border-box;margin:0;padding:0}
  html,body{width:1200px;height:1200px;overflow:hidden;background:var(--stage);font-family:"Lato",sans-serif}
  .flyer{position:absolute;left:175px;top:50px;width:850px;height:1100px;background:var(--paper);overflow:hidden;box-shadow:0 6px 24px rgba(0,0,0,.12)}
  .abs{position:absolute}
  .hero-photo{left:0;top:0;width:850px;height:480px;background:linear-gradient(100deg,#f4f6f8 0%,#e9edf1 40%,#d9dde2 65%,#c9ced4 100%)}
  .header-art{left:0;top:0}
  .brand{left:34px;top:62px;font-family:"Lato",sans-serif;font-weight:900;font-size:31px;letter-spacing:.5px;color:var(--ink)}
  .headline{left:60px;top:212px;font-family:"Anton",sans-serif;line-height:1;color:var(--ink);text-transform:uppercase}
  .headline .l1{font-size:64px}
  .headline .l2{font-size:58px;color:var(--red);margin-top:2px}
  .headline .l3{font-size:39px;margin-top:4px}
  .benefits{left:497px;top:366px;width:332px;height:400px;background:linear-gradient(180deg,#f2070c,#d5050a);border-radius:14px;padding:70px 20px 0 24px;color:#fff}
  .benefits-tab{left:478px;top:390px;background:var(--charcoal);color:#fff;font-weight:900;font-size:23px;padding:4px 18px 5px 12px;border-radius:0 4px 4px 0}
  .tick-list{list-style:none}
  .tick-list li{position:relative;padding-left:25px;font-size:12.5px;font-weight:700;line-height:1.3;margin-bottom:17px}
  .tick-list li svg{position:absolute;left:0;top:0}
  .content{left:32px;top:500px;width:412px;color:var(--text);font-size:12.5px;line-height:1.32}
  .content h2{color:var(--red);font-size:17px;font-weight:900;margin-bottom:12px}
  .content p{margin-bottom:15px}
  .rates{margin:14px 0 30px}
  .rate{display:flex;gap:6px;margin-bottom:6px;font-size:11.5px;font-weight:700}
  .rate .label{width:272px;background:var(--grey-bar);padding:2px 6px;color:#333}
  .rate .value{flex:1;background:var(--red);color:#fff;text-align:center;padding:2px 0}
  .also{left:507px;top:788px;width:320px;color:var(--text)}
  .also h3{color:var(--red);font-size:17px;font-weight:900;margin-bottom:14px}
  .also .tick-list li{font-weight:400;font-size:13.5px;margin-bottom:8px;padding-left:24px}
  .footnote{margin-top:22px;font-size:9.5px;line-height:1.25;color:#555}
  .footer-art{left:0;top:950px}
  .call{left:34px;top:1000px;color:#fff}
  .call .lead{font-size:27px;font-weight:700}
  .call .phone{font-size:42px;font-weight:700;line-height:1.05}
  .contact{top:1038px;display:flex;align-items:center;gap:10px;color:#fff;font-size:12.5px;font-weight:700}
  .contact.mail{left:368px}
  .contact.web{left:634px}
</style>
</head>
<body>
<main class="flyer">
  <div class="abs hero-photo" role="img" aria-label="Photo of a smiling senior couple embracing in a bright home interior"></div>

  <svg class="abs header-art" width="850" height="480" viewBox="0 0 850 480" aria-hidden="true">
    <path d="M0 0 H470 C420 110 300 185 0 180 Z" fill="var(--paper)"/>
    <path d="M470 0 C420 110 300 185 0 180" fill="none" stroke="var(--ink)" stroke-width="10"/>
    <path d="M485 0 C435 125 310 200 0 196" fill="none" stroke="var(--red)" stroke-width="4"/>
    <path d="M0 420 C250 470 560 440 850 350 V480 H0 Z" fill="var(--paper)"/>
    <path d="M0 410 C250 455 560 428 850 345" fill="none" stroke="var(--charcoal)" stroke-width="14"/>
    <path d="M0 438 C250 482 560 452 850 372" fill="none" stroke="var(--red)" stroke-width="4"/>
  </svg>

  <div class="abs brand">CORVANT SHIELD</div>

  <h1 class="abs headline">
    <div class="l1">Our</div>
    <div class="l2">Plans Are</div>
    <div class="l3">Based On Yours</div>
  </h1>

  <section class="abs benefits">
    <ul class="tick-list">
      <li><svg width="15" height="15" viewBox="0 0 16 16"><circle cx="8" cy="8" r="6.8" fill="none" stroke="#fff" stroke-width="1.4"/><path d="M5 8.2l2 2 4-4.2" fill="none" stroke="#fff" stroke-width="1.6"/></svg>All plans we offer are state regulated</li>
      <li><svg width="15" height="15" viewBox="0 0 16 16"><circle cx="8" cy="8" r="6.8" fill="none" stroke="#fff" stroke-width="1.4"/><path d="M5 8.2l2 2 4-4.2" fill="none" stroke="#fff" stroke-width="1.6"/></svg>Relatively low monthly premiums</li>
      <li><svg width="15" height="15" viewBox="0 0 16 16"><circle cx="8" cy="8" r="6.8" fill="none" stroke="#fff" stroke-width="1.4"/><path d="M5 8.2l2 2 4-4.2" fill="none" stroke="#fff" stroke-width="1.6"/></svg>Premiums can never increase</li>
      <li><svg width="15" height="15" viewBox="0 0 16 16"><circle cx="8" cy="8" r="6.8" fill="none" stroke="#fff" stroke-width="1.4"/><path d="M5 8.2l2 2 4-4.2" fill="none" stroke="#fff" stroke-width="1.6"/></svg>Your policy can never be cancelled as long as you pay your premium</li>
      <li><svg width="15" height="15" viewBox="0 0 16 16"><circle cx="8" cy="8" r="6.8" fill="none" stroke="#fff" stroke-width="1.4"/><path d="M5 8.2l2 2 4-4.2" fill="none" stroke="#fff" stroke-width="1.6"/></svg>No medical exams</li>
      <li><svg width="15" height="15" viewBox="0 0 16 16"><circle cx="8" cy="8" r="6.8" fill="none" stroke="#fff" stroke-width="1.4"/><path d="M5 8.2l2 2 4-4.2" fill="none" stroke="#fff" stroke-width="1.6"/></svg>Guaranteed Death Benefit</li>
      <li><svg width="15" height="15" viewBox="0 0 16 16"><circle cx="8" cy="8" r="6.8" fill="none" stroke="#fff" stroke-width="1.4"/><path d="M5 8.2l2 2 4-4.2" fill="none" stroke="#fff" stroke-width="1.6"/></svg>Many policies we offer are Guaranteed Acceptance, "Day 1" coverage, have a child/grandchild rider and/or have an accelerated death benefit rider</li>
    </ul>
  </section>
  <div class="abs benefits-tab">Benefits:</div>

  <section class="abs content">
    <h2>Final Expense Insurance</h2>
    <p>Final Expense Insurance is a type of permanent life insurance where the death benefit is used to cover (but not limited to) medical costs, funeral costs and other end-of-life expenses. It is a budget friendly option with a death benefit of up to $40k.</p>
    <div class="rates">
      <div class="rate"><span class="label">Monthly premiums as low as</span><span class="value">$11*</span></div>
      <div class="rate"><span class="label">Death Benefits as high as</span><span class="value">$40,000</span></div>
    </div>
    <p>Unforeseen events and a lack of the right kind of insurance can spell trouble quickly. Contact us today, to set up a free assessment time. We will analyze your insurance needs and get you and your family the right coverage quickly at a budget friendly price.</p>
    <p>We have been helping clients in Northern Idaho/Eastern Washington prepare for the unknown.</p>
    <p>We have access to the industry's top insurance carriers so you can get the right coverage, that fits your budget.</p>
    <p>Find out how we can give you the peace of mind knowing your family wont have a financial burden if something were to happen to you.</p>
  </section>

  <section class="abs also">
    <h3>We Also Specialize In:</h3>
    <ul class="tick-list">
      <li><svg width="15" height="15" viewBox="0 0 16 16"><circle cx="8" cy="8" r="6.8" fill="none" stroke="var(--red)" stroke-width="1.4"/><path d="M5 8.2l2 2 4-4.2" fill="none" stroke="var(--red)" stroke-width="1.6"/></svg>Medicare Supplement Insurance (Medigap)</li>
      <li><svg width="15" height="15" viewBox="0 0 16 16"><circle cx="8" cy="8" r="6.8" fill="none" stroke="var(--red)" stroke-width="1.4"/><path d="M5 8.2l2 2 4-4.2" fill="none" stroke="var(--red)" stroke-width="1.6"/></svg>Annuities</li>
      <li><svg width="15" height="15" viewBox="0 0 16 16"><circle cx="8" cy="8" r="6.8" fill="none" stroke="var(--red)" stroke-width="1.4"/><path d="M5 8.2l2 2 4-4.2" fill="none" stroke="var(--red)" stroke-width="1.6"/></svg>Mortgage Protection Insurance</li>
    </ul>
    <p class="footnote">*Based on an insured that is a 65 year old, non-smoking female that has no medical conditions with a death benefit of $2k</p>
  </section>

  <svg class="abs footer-art" width="850" height="150" viewBox="0 0 850 150" aria-hidden="true">
    <defs>
      <linearGradient id="footerRed" x1="0" y1="0" x2="0" y2="1">
        <stop offset="0" stop-color="#ee080d"/>
        <stop offset="1" stop-color="var(--red-deep)"/>
      </linearGradient>
    </defs>
    <path d="M0 30 C260 10 520 70 850 8 V150 H0 Z" fill="url(#footerRed)"/>
    <path d="M0 22 C260 2 520 62 850 0" fill="none" stroke="var(--charcoal)" stroke-width="7"/>
  </svg>

  <div class="abs call">
    <div class="lead">Call us now:</div>
    <div class="phone">(555)214.7730</div>
  </div>

  <div class="abs contact mail">
    <svg width="32" height="32" viewBox="0 0 32 32"><circle cx="16" cy="16" r="14.5" fill="none" stroke="#fff" stroke-width="1.6"/><rect x="9" y="11" width="14" height="10" rx="1" fill="none" stroke="#fff" stroke-width="1.6"/><path d="M9 11.5l7 5.5 7-5.5" fill="none" stroke="#fff" stroke-width="1.6"/></svg>
    <span>tkelwer@corvantshield.com</span>
  </div>
  <div class="abs contact web">
    <svg width="32" height="32" viewBox="0 0 32 32"><circle cx="16" cy="16" r="14.5" fill="none" stroke="#fff" stroke-width="1.6"/><circle cx="16" cy="16" r="7.5" fill="none" stroke="#fff" stroke-width="1.5"/><ellipse cx="16" cy="16" rx="3.2" ry="7.5" fill="none" stroke="#fff" stroke-width="1.3"/><path d="M8.5 16h15" stroke="#fff" stroke-width="1.3"/></svg>
    <span>corvantshield.com</span>
  </div>
</main>
</body>
</html>
```